Business card for my new company (Accounting firm)

I need a business card for my new business Brightwell Advisory and Ledger SA. Our services are accounting, tax, audit and financial management. Our customers are small companies, start-ups and new companies. The final design has to show financial security, trust and growth. Please find our logo attached to the business card. Text for the business card: Brightwell Advisory and Ledger SA Tomas Varenholt Director and Founder Certified Accountant Tel. 022 418 57 34 tv@clairevalconseil.ch www.clairevalconseil.ch Rue des Vergières 27 1201 Geneva
Target Market(s)
Our customers are small companies, start-ups and new companies.
Industry/Entity Type
Finance And Accounting
Contact Information for Business Card
Claireval Conseil et Comptes SA
Tomas Varenholt
Directeur et Fondateur
Expert-comptable diplômé
Tél. 022 418 57 34
tv@clairevalconseil.ch
www.clairevalconseil.ch
Rue des Vergières 27
1201 Genève

```html
<!DOCTYPE html>
<html lang="fr">
<head>
<meta charset="utf-8">
<title>Claireval Conseil et Comptes SA – Carte de visite</title>
<link rel="stylesheet" href="https://fonts.googleapis.com/css2?family=Raleway:wght@400;500;600;700&display=swap">
<style>
  :root {
    --backdrop: #7a7a7a;
    --card-white: #f3f3f3;
    --brand-blue: #1b5a8e;
    --brand-deep: #154a76;
    --brand-sky: #2a93cf;
    --text-grey: #4f5257;
    --mark-grey: #3a3d42;
    --white: #ffffff;
  }
  * { margin: 0; padding: 0; box-sizing: border-box; }
  html, body {
    width: 1200px; height: 960px; overflow: hidden;
    background: var(--backdrop);
    font-family: "Raleway", sans-serif;
  }
  .canvas { position: relative; width: 1200px; height: 960px; }

  .card {
    position: absolute; left: 270px; width: 662px; height: 378px;
    border-radius: 22px; overflow: hidden;
  }

  /* Front */
  .card-front { top: 73px; }
  .front-photo {
    position: absolute; inset: 0;
    background: linear-gradient(160deg, #24699b 0%, #1a5c8c 45%, #12466f 100%);
  }
  .front-name {
    position: absolute; left: 0; right: 0; top: 150px;
    text-align: center; color: var(--white);
    font-size: 46px; font-weight: 600; letter-spacing: 1px;
  }
  .front-web {
    position: absolute; left: 0; right: 0; top: 319px;
    text-align: center; color: var(--white); font-size: 15px;
  }

  /* Back */
  .card-back { top: 508px; background: var(--card-white); }
  .brand-square {
    position: absolute; left: 78px; top: 48px;
    width: 60px; height: 60px; background: var(--brand-blue);
  }
  .brand-name {
    position: absolute; left: 48px; top: 134px;
    font-size: 31px; font-weight: 600; color: var(--mark-grey);
  }
  .person {
    position: absolute; right: 54px; top: 122px; text-align: right;
  }
  .person-name { font-size: 19px; font-weight: 700; color: var(--brand-blue); line-height: 24px; }
  .person-role { font-size: 14.5px; color: var(--text-grey); line-height: 19px; }

  .company {
    position: absolute; left: 47px; top: 221px;
    font-size: 15px; line-height: 19px; color: var(--text-grey);
  }
  .company-name { color: var(--brand-blue); }
  .rule {
    position: absolute; left: 47px; top: 292px;
    width: 26px; height: 2px; background: var(--brand-blue);
  }
  .contacts {
    position: absolute; left: 47px; top: 311px;
    font-size: 15px; line-height: 19px; color: var(--text-grey);
  }
  .contact-line { display: flex; align-items: center; gap: 9px; }
  .contact-line svg { width: 13px; height: 13px; flex: none; }

  .footer-band {
    position: absolute; left: 0; bottom: 0; width: 420px; height: 7px;
    background: var(--brand-sky);
  }
  .footer-web {
    position: absolute; left: 422px; bottom: 0; width: 198px; height: 26px;
    background: var(--brand-deep);
    clip-path: polygon(8px 0, 100% 0, 100% 100%, 0 100%);
    color: var(--white); font-size: 15px; line-height: 26px;
    padding-left: 32px;
  }
  .footer-tab {
    position: absolute; left: 623px; bottom: 0; width: 39px; height: 26px;
    background: var(--brand-sky);
  }
</style>
</head>
<body>
<main class="canvas">
  <section class="card card-front">
    <div class="front-photo" role="img" aria-label="Photo teintée en bleu d'un stylo posé sur une calculatrice"></div>
    <div class="front-name">Claireval</div>
    <div class="front-web">www.clairevalconseil.ch</div>
  </section>

  <section class="card card-back">
    <div class="brand-square"></div>
    <div class="brand-name">Claireval</div>

    <div class="person">
      <div class="person-name">Tomas Varenholt</div>
      <div class="person-role">Directeur et Fondateur</div>
      <div class="person-role">Expert - Comptable Diplômé</div>
    </div>

    <div class="company">
      <div class="company-name">Claireval Conseil et Comptes SA</div>
      <div>Rue des Vergières 27</div>
      <div>1201 Genève</div>
    </div>

    <div class="rule"></div>

    <div class="contacts">
      <div class="contact-line">
        <svg viewBox="0 0 24 24" aria-hidden="true"><path fill="#1b5a8e" d="M6.6 10.8a15.1 15.1 0 0 0 6.6 6.6l2.2-2.2c.3-.3.7-.4 1-.2 1.1.4 2.3.6 3.6.6.6 0 1 .4 1 1V20c0 .6-.4 1-1 1A17 17 0 0 1 3 4c0-.6.4-1 1-1h3.5c.6 0 1 .4 1 1 0 1.3.2 2.5.6 3.6.1.3 0 .7-.2 1z"/></svg>
        <span>022 418 57 34</span>
      </div>
      <div class="contact-line">
        <svg viewBox="0 0 24 24" aria-hidden="true"><rect x="2" y="5" width="20" height="14" fill="none" stroke="#1b5a8e" stroke-width="2"/><path d="M2 5l10 8 10-8" fill="none" stroke="#1b5a8e" stroke-width="2"/></svg>
        <span>tv@clairevalconseil.ch</span>
      </div>
    </div>

    <div class="footer-band"></div>
    <div class="footer-web">www.clairevalconseil.ch</div>
    <div class="footer-tab"></div>
  </section>
</main>
</body>
</html>
```